New Dental Office Needs an Attractive and user friendly Website Designed

I need a website for a new dental office. The Name is Harrowfield Dentistry. I would like a Modern design with a user friendly interface and usability.
I would like a landing page, a page that lists the services we offer: Cosmetic Dentistry, Implants, Dental Hygiene, Emergency Services, Restorations, Dentures
Target Market(s)
Mid to upper class
Industry/Entity Type
Dentistry
Coding
Number of Pages Required
1 page
Requirements
Must have
- Landing page that has a scheduling option, Procedures, operating hours, and contact us info
Nice to have
- Appealing design, Soft comforting colors. Easy to navigate page, Modern and professional.

```html
<!DOCTYPE html>
<html lang="en">
<head>
<meta charset="utf-8">
<title>Harrowfield Dentistry</title>
<link href="https://fonts.googleapis.com/css2?family=Poppins:wght@400;500;600;700&display=swap" rel="stylesheet">
<style>
:root{
  --blue:#1a8fdc;
  --blue-dark:#0f74b8;
  --navy:#0e2a44;
  --text:#4a5a6a;
  --sky:#eaf5fc;
  --sky-2:#d6ecfa;
  --line:#d9e6ef;
  --white:#ffffff;
  --star:#f5b301;
}
*{margin:0;padding:0;box-sizing:border-box}
html,body{width:1200px;height:3892px;overflow:hidden}
body{font-family:"Poppins",sans-serif;color:var(--text);background:var(--white);position:relative}
.abs{position:absolute}
a{color:inherit;text-decoration:none}

/* top bar */
.topbar{position:absolute;left:0;top:0;width:1200px;height:32px;background:var(--blue);color:var(--white);font-size:12px;display:flex;align-items:center;padding:0 64px}
.topbar .item{display:flex;align-items:center;gap:6px;margin-right:26px}
.topbar .socials{margin-left:auto;display:flex;gap:8px}
.dot{width:16px;height:16px;border-radius:50%;background:var(--white);opacity:.9;display:block}

/* nav */
.nav{position:absolute;left:0;top:32px;width:1200px;height:120px;display:flex;align-items:center;padding:0 64px}
.brand{font-size:22px;font-weight:600;color:var(--navy);display:flex;align-items:center;gap:10px;line-height:1}
.brand .mark{width:14px;height:14px;border-radius:50%;background:var(--blue)}
.menu{display:flex;gap:34px;margin-left:auto;margin-right:40px;font-size:14px;font-weight:500;color:var(--navy)}
.menu .active{color:var(--blue);border-bottom:2px solid var(--blue);padding-bottom:4px}
.btn{display:inline-flex;align-items:center;justify-content:center;gap:8px;border-radius:30px;font-size:13px;font-weight:500;letter-spacing:.3px}
.btn-fill{background:var(--blue);color:var(--white)}
.btn-line{border:2px solid var(--blue);color:var(--blue);background:var(--white)}
.nav .btn{width:216px;height:44px}

/* hero */
.hero{position:absolute;left:0;top:152px;width:1200px;height:488px;background:linear-gradient(90deg,#f4f9fd 0%,var(--sky) 60%,#dff0fb 100%);overflow:hidden}
.hero h1{position:absolute;left:112px;top:82px;font-size:46px;line-height:1.15;font-weight:700;color:var(--navy)}
.hero p{position:absolute;left:112px;top:220px;font-size:16px}
.hero .cta{position:absolute;left:112px;top:272px;display:flex;gap:20px}
.hero .cta .btn{height:46px;padding:0 26px}
.ring{position:absolute;border-radius:50%}
.ring.r1{left:628px;top:0;width:500px;height:500px;background:#d4ebfa}
.ring.r2{left:660px;top:20px;width:440px;height:440px;border:14px solid var(--blue);background:var(--white)}
.hero-photo{position:absolute;left:690px;top:50px;width:380px;height:380px;border-radius:50%;background:linear-gradient(160deg,#e7f2f9,#b9d7ea 60%,#7fb3d6)}

/* welcome */
.welcome-photo{position:absolute;left:112px;top:688px;width:456px;height:312px;border-radius:6px;background:linear-gradient(135deg,#cfe4f2,#8fbfdf 55%,#e9f1f6)}
.welcome h2{position:absolute;left:600px;top:706px;font-size:40px;line-height:1.2;font-weight:600;color:var(--navy)}
.welcome .copy{position:absolute;left:600px;top:828px;width:488px;border-left:3px solid var(--blue);padding-left:18px;font-size:14.5px;line-height:1.72}
.welcome .copy strong{color:var(--navy);font-weight:600}

/* section headings */
.sec-title{font-size:40px;line-height:1.15;font-weight:600;color:var(--navy)}
.sec-title span{display:flex;align-items:center;gap:14px;font-size:34px}
.sec-title span::after{content:"";width:60px;height:3px;background:var(--blue);display:block}
.sec-title span.blue{color:var(--blue)}

/* services */
.services-title{position:absolute;left:112px;top:1086px}
.services-btn{position:absolute;left:856px;top:1116px;width:232px;height:46px}
.card{position:absolute;width:268px;height:340px;border:1px solid var(--line);border-radius:8px;background:var(--white);overflow:hidden}
.card .top{height:150px;background:var(--sky);display:flex;align-items:center;justify-content:center}
.card .icon{width:92px;height:92px;border-radius:12px;background:var(--white);display:flex;align-items:center;justify-content:center;box-shadow:0 4px 14px rgba(26,143,220,.12)}
.card h3{font-size:18px;font-weight:500;color:var(--navy);margin:26px 20px 8px}
.card p{font-size:13px;line-height:1.55;margin:0 20px;height:42px;overflow:hidden}
.card .more{display:inline-block;margin:12px 20px 0;font-size:13px;color:var(--blue);border-bottom:1px solid var(--blue)}

/* booking */
.book{position:absolute;left:112px;top:2120px;width:976px;height:340px;border-radius:10px;overflow:hidden;background:var(--blue)}
.book h2{position:absolute;left:48px;top:56px;font-size:34px;font-weight:600;color:var(--white)}
.book p{position:absolute;left:48px;top:120px;width:400px;font-size:14px;line-height:1.6;color:#e4f2fc}
.book .btn{position:absolute;left:48px;top:220px;width:202px;height:46px;background:var(--white);color:var(--navy)}
.book-photo{position:absolute;left:488px;top:0;width:488px;height:340px;background:linear-gradient(120deg,#d9e9f3,#a8cce3 50%,#e8d9cc)}

/* hours */
.hours-photo{position:absolute;left:112px;top:2576px;width:456px;height:364px;border-radius:6px;background:linear-gradient(140deg,#d7e8f3,#8db9d6 55%,#eef4f7)}
.hours-title{position:absolute;left:600px;top:2598px}
.hours-table{position:absolute;left:600px;top:2732px;width:488px;height:208px;background:var(--blue);border-radius:6px;color:var(--white);padding:22px 30px;font-size:15px}
.hours-table table{width:100%;border-collapse:collapse}
.hours-table th{text-align:left;font-weight:500;font-size:18px;padding-bottom:10px;border-bottom:1px solid rgba(255,255,255,.45)}
.hours-table td{padding:9px 0 0}
.hours-table td:nth-child(2),.hours-table th:nth-child(2){padding-left:20px}

/* testimonials */
.testi-title{position:absolute;left:112px;top:2990px}
.testi-lead{position:absolute;left:112px;top:3120px;width:380px;font-size:14px;line-height:1.6}
.quote{position:absolute;left:600px;top:2984px;width:488px;font-size:18px;font-weight:600;color:var(--navy);line-height:1.55}
.author{position:absolute;left:630px;top:3120px;display:flex;align-items:center;gap:12px;font-size:15px;font-weight:600;color:var(--navy)}
.avatar{width:44px;height:44px;border-radius:50%;background:linear-gradient(135deg,#f0d9c6,#c99d82)}
.stars{color:var(--star);font-size:16px;letter-spacing:1px}
.arrow{position:absolute;width:28px;height:28px;border-radius:50%;background:var(--blue);display:flex;align-items:center;justify-content:center}

/* newsletter */
.newsletter{position:absolute;left:112px;top:3300px;width:976px;height:220px;border-radius:10px;background:linear-gradient(90deg,var(--sky),#cfe8f8)}
.newsletter h2{position:absolute;left:44px;top:52px;font-size:30px;font-weight:600;color:var(--navy)}
.newsletter p{position:absolute;left:44px;top:106px;width:420px;font-size:13.5px;line-height:1.6}
.newsletter .field{position:absolute;left:560px;top:86px;width:230px;height:48px;border-radius:30px;background:var(--white);font-size:13px;display:flex;align-items:center;padding-left:22px;color:#7b8a98}
.newsletter .btn{position:absolute;left:800px;top:86px;width:140px;height:48px}

/* footer */
.footer{position:absolute;left:0;top:3600px;width:1200px}
.footer .brand{position:absolute;left:112px;top:8px;font-size:20px}
.footer .tag{position:absolute;left:112px;top:48px;width:200px;font-size:12px;line-height:1.5}
.footer .fsoc{position:absolute;left:112px;top:96px;display:flex;gap:8px}
.footer .fsoc .dot{background:var(--blue);width:22px;height:22px}
.fcol{position:absolute;top:8px;font-size:13px;line-height:1.95}
.fcol h4{font-size:15px;font-weight:600;color:var(--blue);margin-bottom:6px}
.fcol .row{display:flex;align-items:flex-start;gap:8px}
.fcol .row svg{margin-top:6px;flex:none}
.copyright{position:absolute;left:0;top:3858px;width:1200px;height:34px;border-top:1px solid var(--line);display:flex;align-items:center;justify-content:center;font-size:12px}
</style>
</head>
<body>

<header>
  <div class="topbar">
    <span class="item">
      <svg width="12" height="12" viewBox="0 0 24 24" fill="#fff"><path d="M6.6 10.8a15.1 15.1 0 0 0 6.6 6.6l2.2-2.2c.3-.3.7-.4 1-.2 1.1.4 2.3.6 3.6.6.6 0 1 .4 1 1V20c0 .6-.4 1-1 1A17 17 0 0 1 3 4c0-.6.4-1 1-1h3.5c.6 0 1 .4 1 1 0 1.3.2 2.5.6 3.6.1.3 0 .7-.2 1z"/></svg>
      (555) 014-2290
    </span>
    <span class="item">
      <svg width="12" height="12" viewBox="0 0 24 24" fill="#fff"><path d="M12 2a7 7 0 0 0-7 7c0 5.2 7 13 7 13s7-7.8 7-13a7 7 0 0 0-7-7zm0 9.5A2.5 2.5 0 1 1 12 6.5a2.5 2.5 0 0 1 0 5z"/></svg>
      48 Harrowfield Lane, Millbrook, ST 00000
    </span>
    <span class="socials"><i class="dot"></i><i class="dot"></i><i class="dot"></i><i class="dot"></i></span>
  </div>

  <nav class="nav">
    <div class="brand"><span class="mark"></span>Harrowfield Dentistry</div>
    <div class="menu">
      <a class="active">HOME</a><a>ABOUT</a><a>SERVICES</a><a>SCHEDULE</a><a>CONTACT</a>
    </div>
    <a class="btn btn-fill">BOOK APPOINTMENT</a>
  </nav>
</header>

<section class="hero">
  <h1>Modern Care.<br>Timeless Smiles.</h1>
  <p>Trusted dental care in a calm, welcoming environment.</p>
  <div class="cta">
    <a class="btn btn-fill">BOOK APPOINTMENT</a>
    <a class="btn btn-line">
      <svg width="14" height="14" viewBox="0 0 24 24" fill="#1a8fdc"><path d="M6.6 10.8a15.1 15.1 0 0 0 6.6 6.6l2.2-2.2c.3-.3.7-.4 1-.2 1.1.4 2.3.6 3.6.6.6 0 1 .4 1 1V20c0 .6-.4 1-1 1A17 17 0 0 1 3 4c0-.6.4-1 1-1h3.5c.6 0 1 .4 1 1 0 1.3.2 2.5.6 3.6.1.3 0 .7-.2 1z"/></svg>
      (555) 014-2290
    </a>
  </div>
  <div class="ring r1"></div>
  <div class="ring r2"></div>
  <div class="hero-photo" role="img" aria-label="Portrait photo of a smiling dentist in a white coat and mask"></div>
</section>

<section class="welcome">
  <div class="welcome-photo" role="img" aria-label="Photo of a dentist treating a patient in a modern clinic"></div>
  <h2>Welcome to<br>Harrowfield Dentistry</h2>
  <p class="copy">At Harrowfield Dentistry, we believe that a healthy, confident smile can change your life. Our modern, state-of-the-art clinic is built around the core values of <strong>comfort, compassion, and excellence.</strong> From your very first visit, we aim to create a welcoming and relaxed environment that feels more like a home than a clinic.</p>
</section>

<section class="services">
  <h2 class="sec-title services-title">Comprehensive<span class="blue">Dental Services</span></h2>
  <a class="btn btn-fill services-btn">EXPLORE ALL SERVICES</a>

  <article class="card" style="left:112px;top:1248px">
    <div class="top"><div class="icon">
      <svg width="52" height="52" viewBox="0 0 48 48" fill="none" stroke="#1a8fdc" stroke-width="2.2" stroke-linejoin="round"><path d="M14 8c-5 0-8 4-8 9 0 6 3 9 4 15 1 5 2 9 5 9s3-9 9-9 6 9 9 9 4-4 5-9c1-6 4-9 4-15 0-5-3-9-8-9-4 0-6 2-10 2S18 8 14 8z"/><path d="M36 4l1.5 3 3 1.5-3 1.5L36 13l-1.5-3-3-1.5 3-1.5z"/></svg>
    </div></div>
    <h3>Cosmetic Dentistry</h3>
    <p>Transform your smile with our advanced cosmetic treatments.</p>
    <a class="more">Learn More</a>
  </article>

  <article class="card" style="left:466px;top:1248px">
    <div class="top"><div class="icon">
      <svg width="52" height="52" viewBox="0 0 48 48" fill="none" stroke="#1a8fdc" stroke-width="2.2" stroke-linejoin="round"><path d="M14 6c-5 0-8 4-8 8 0 5 4 7 6 9h24c2-2 6-4 6-9 0-4-3-8-8-8-4 0-6 2-10 2s-6-2-10-2z"/><path d="M18 23h12l-2 5h-8z"/><path d="M19 31h10M20 35h8M21 39h6M22 43h4"/></svg>
    </div></div>
    <h3>Dental Implants</h3>
    <p>A permanent solution for missing teeth. Our experts place each implant with care.</p>
    <a class="more">Learn More</a>
  </article>

  <article class="card" style="left:820px;top:1248px">
    <div class="top"><div class="icon">
      <svg width="52" height="52" viewBox="0 0 48 48" fill="none" stroke="#1a8fdc" stroke-width="2.2" stroke-linejoin="round"><path d="M12 16c-4 0-6 3-6 7 0 5 3 7 3 12 0 4 2 7 4 7s3-7 7-7 5 7 7 7 4-3 4-7c0-5 3-7 3-12 0-4-2-7-6-7-3 0-5 2-8 2s-5-2-8-2z"/><path d="M40 4v14M36 6h8M36 10h8M36 14h8"/></svg>
    </div></div>
    <h3>Dental Hygiene</h3>
    <p>Prevent problems before they start. Our thorough cleanings keep you healthy.</p>
    <a class="more">Learn More</a>
  </article>

  <article class="card" style="left:112px;top:1640px">
    <div class="top"><div class="icon">
      <svg width="52" height="52" viewBox="0 0 48 48" fill="none" stroke="#1a8fdc" stroke-width="2.2" stroke-linejoin="round"><rect x="6" y="12" width="30" height="26" rx="3"/><path d="M16 12V8h10v4M21 19v12M15 25h12"/><circle cx="38" cy="36" r="7"/><path d="M38 32v4l3 2"/></svg>
    </div></div>
    <h3>Emergency Services</h3>
    <p>Tooth pain or dental injury? We're here when you need us most, fast.</p>
    <a class="more">Learn More</a>
  </article>

  <article class="card" style="left:466px;top:1640px">
    <div class="top"><div class="icon">
      <svg width="52" height="52" viewBox="0 0 48 48" fill="none" stroke="#1a8fdc" stroke-width="2.2" stroke-linejoin="round"><path d="M12 14c-4 0-6 3-6 7 0 5 3 7 3 12 0 4 2 7 4 7s3-7 7-7 5 7 7 7 4-3 4-7c0-5 3-7 3-12 0-4-2-7-6-7-3 0-5 2-8 2s-5-2-8-2z"/><path d="M30 12l10-8 4 4-8 10-4-1z"/></svg>
    </div></div>
    <h3>Restorations</h3>
    <p>From fillings to crowns, we repair and restore damaged teeth with care.</p>
    <a class="more">Learn More</a>
  </article>

  <article class="card" style="left:820px;top:1640px">
    <div class="top"><div class="icon">
      <svg width="52" height="52" viewBox="0 0 48 48" fill="none" stroke="#1a8fdc" stroke-width="2.2" stroke-linejoin="round"><path d="M6 20c0-8 8-12 18-12s18 4 18 12"/><path d="M6 20h36v6H6z"/><path d="M10 26v6a3 3 0 0 0 6 0v-6M16 26v6a3 3 0 0 0 6 0v-6M22 26v6a3 3 0 0 0 6 0v-6M28 26v6a3 3 0 0 0 6 0v-6M34 26v6a3 3 0 0 0 6 0v-6"/></svg>
    </div></div>
    <h3>Dentures</h3>
    <p>Comfortable, natural-looking dentures tailored to you. Whether full or partial.</p>
    <a class="more">Learn More</a>
  </article>
</section>

<section class="book">
  <h2>Book Your Visit Today</h2>
  <p>It only takes a minute to schedule your next appointment. Convenient online booking and flexible hours to fit your lifestyle.</p>
  <a class="btn">SCHEDULE NOW
    <svg width="14" height="14" viewBox="0 0 24 24" fill="none" stroke="#0e2a44" stroke-width="2.5"><path d="M4 12h15M13 6l6 6-6 6"/></svg>
  </a>
  <div class="book-photo" role="img" aria-label="Photo of a dentist showing a family their treatment plan"></div>
</section>

<section class="hours">
  <div class="hours-photo" role="img" aria-label="Photo of a dentist examining a patient in the treatment chair"></div>
  <h2 class="sec-title hours-title">We're Open<span>When You Need Us</span></h2>
  <div class="hours-table">
    <table>
      <tr><th>Day</th><th>Hours</th></tr>
      <tr><td>Monday – Thursday</td><td>09 AM – 06 PM</td></tr>
      <tr><td>Friday</td><td>09 AM – 02 PM</td></tr>
      <tr><td>Sat – Sunday</td><td>Closed</td></tr>
    </table>
  </div>
</section>

<section class="testimonials">
  <h2 class="sec-title testi-title">What Our<span>Patients Are Saying</span></h2>
  <p class="testi-lead">We take pride in delivering gentle, personalized care – and our patients agree.</p>
  <span class="arrow" style="left:566px;top:2996px"><svg width="12" height="12" viewBox="0 0 24 24" fill="none" stroke="#fff" stroke-width="3"><path d="M15 5l-7 7 7 7"/></svg></span>
  <blockquote class="quote" style="left:614px;width:440px">Best dental experience I've ever had! The staff is incredibly friendly, and Dr. Morgan made me feel completely at ease.</blockquote>
  <div class="author"><span class="avatar" role="img" aria-label="Patient photo"></span><span>— Claire D.<br><span class="stars">★★★★★</span></span></div>
  <span class="arrow" style="left:1092px;top:2996px"><svg width="12" height="12" viewBox="0 0 24 24" fill="none" stroke="#fff" stroke-width="3"><path d="M9 5l7 7-7 7"/></svg></span>
</section>

<section class="newsletter">
  <h2>Subscribe to Our Newsletter</h2>
  <p>Be the first to know about special promotions, dental care tips, new services, and important updates.</p>
  <div class="field">Your Mail Address</div>
  <a class="btn btn-fill">SIGN UP
    <svg width="14" height="14" viewBox="0 0 24 24" fill="none" stroke="#fff" stroke-width="2.5"><path d="M4 12h15M13 6l6 6-6 6"/></svg>
  </a>
</section>

<footer class="footer">
  <div class="brand"><span class="mark"></span>Harrowfield Dentistry</div>
  <p class="tag">We're here to help you smile brighter every day.</p>
  <div class="fsoc"><i class="dot"></i><i class="dot"></i><i class="dot"></i><i class="dot"></i></div>

  <div class="fcol" style="left:380px">
    <h4>Quick Links</h4>
    Home<br>Services<br>Schedule Appointment<br>Contact Us<br>Privacy Policy
  </div>

  <div class="fcol" style="left:600px">
    <h4>Contact</h4>
    <div class="row"><svg width="12" height="12" viewBox="0 0 24 24" fill="#1a8fdc"><path d="M12 2a7 7 0 0 0-7 7c0 5.2 7 13 7 13s7-7.8 7-13a7 7 0 0 0-7-7zm0 9.5A2.5 2.5 0 1 1 12 6.5a2.5 2.5 0 0 1 0 5z"/></svg><span>48 Harrowfield Lane,<br>Millbrook, ST 00000</span></div>
    <div class="row"><svg width="12" height="12" viewBox="0 0 24 24" fill="#1a8fdc"><path d="M6.6 10.8a15.1 15.1 0 0 0 6.6 6.6l2.2-2.2c.3-.3.7-.4 1-.2 1.1.4 2.3.6 3.6.6.6 0 1 .4 1 1V20c0 .6-.4 1-1 1A17 17 0 0 1 3 4c0-.6.4-1 1-1h3.5c.6 0 1 .4 1 1 0 1.3.2 2.5.6 3.6.1.3 0 .7-.2 1z"/></svg><span>(555) 014-2290</span></div>
    <div class="row"><svg width="12" height="12" viewBox="0 0 24 24" fill="none" stroke="#1a8fdc" stroke-width="2.4"><rect x="3" y="5" width="18" height="14" rx="2"/><path d="M3 7l9 6 9-6"/></svg><span>info@harrowfielddentistry.com</span></div>
  </div>

  <div class="fcol" style="left:864px">
    <h4>Office Hours</h4>
    Mon – Thu: 9:00 AM – 6:00 PM<br>Friday: 9:00 AM – 2:00 PM<br>Saturday – Sunday: Closed
  </div>
</footer>
<div class="copyright">© 2025 Harrowfield Dentistry. All rights reserved.</div>

</body>
</html>
```